Creative Alcoholic Beverage Package Design Needed!

We need a packaging design for a new alcoholic beverage, including the brand name. Flavours will include Sangria and Margarita, and future line extensions as well. Package will be a box (see attached dieline and example of a competitive product) in a 3 liter format. The dimensions of the box need to match the dieline, but we can be creative on the printing of the box. The product inside will be of high-quality, so the design needs to match this
Updates

Need extra days to review

Target Market(s)

25 to 40 year old, 70% female, 30% male

Colors

Designer to choose colors to be used in the design.

Requirements
Must have
• Be attractive, colourful, modern
• clearly mention the flavour, and show the components of the flavour (Sangria : red wine and citrus) - Margarita (mexican inspiration, lime, etc.)
• Have a clear "brand name" along with the flavours
• Mention the quantity (3 liters), alcohol level : 10% alc./vol.

```html
<!DOCTYPE html>
<html lang="en">
<head>
<meta charset="utf-8">
<title>Velora Margarita – 3 Litre Carton</title>
<link rel="stylesheet" href="https://fonts.googleapis.com/css2?family=Oswald:wght@300;400&family=Lora:wght@400;700&family=Open+Sans:wght@400;600&family=Great+Vibes&family=Playfair+Display:wght@700&display=swap">
<style>
  :root{
    --backdrop:#3a3a3c;
    --board:#ffffff;
    --cut:#2b2d86;
    --fold:#e0242a;
    --leaf-dark:#1f5a12;
    --leaf:#4f9a1f;
    --leaf-light:#8cc63f;
    --olive:#8a7a1e;
    --ink:#1d1d1d;
    --cream:#efe7a8;
    --grey-box:#c8c8ca;
  }
  html,body{margin:0;padding:0;width:1200px;height:1200px;overflow:hidden;background:var(--backdrop);}
  .carton{display:block;width:1200px;height:1200px;}
  .panel{fill:var(--board);stroke:var(--cut);stroke-width:2;}
  .fold{stroke:var(--fold);stroke-width:1.6;fill:none;}
  .glue-marks{stroke:var(--cut);stroke-width:1.6;fill:none;}
  .handle{fill:var(--board);stroke:var(--cut);stroke-width:2;}
  .brand-hero{font-family:"Playfair Display",serif;font-weight:700;fill:var(--leaf-dark);}
  .tagline{font-family:"Lora",serif;letter-spacing:2px;fill:var(--ink);}
  .flavour{font-family:"Oswald",sans-serif;font-weight:300;fill:#ffffff;}
  .body-copy{font-family:"Open Sans",sans-serif;fill:var(--olive);}
  .script{font-family:"Great Vibes",cursive;fill:var(--ink);}
  .small-caps{font-family:"Open Sans",sans-serif;font-weight:600;letter-spacing:2px;fill:var(--ink);}
  .contains-title{font-family:"Great Vibes",cursive;fill:var(--leaf-dark);}
  .contains-item{font-family:"Lora",serif;fill:var(--leaf-dark);}
  .volume-num{font-family:"Playfair Display",serif;font-weight:700;fill:var(--ink);font-variant-numeric:lining-nums;}
  .volume-unit{font-family:"Oswald",sans-serif;font-weight:400;letter-spacing:3px;fill:var(--ink);}
  .tiny{font-family:"Open Sans",sans-serif;fill:var(--ink);}
  .abv{font-family:"Lora",serif;fill:var(--ink);}
</style>
</head>
<body>
<svg class="carton" viewBox="0 0 1500 1500" xmlns="http://www.w3.org/2000/svg">
  <defs>
    <linearGradient id="band" x1="0" x2="1">
      <stop offset="0" stop-color="#2f7a16"/>
      <stop offset="0.5" stop-color="#6fb02a"/>
      <stop offset="1" stop-color="#2a6a12"/>
    </linearGradient>
    <radialGradient id="photo-soft" cx="0.5" cy="0.35" r="0.65">
      <stop offset="0" stop-color="#f1eca0"/>
      <stop offset="0.55" stop-color="#f4f1c4"/>
      <stop offset="1" stop-color="#ffffff"/>
    </radialGradient>
  </defs>

  <!-- glue flap -->
  <path class="panel" d="M20 490 L88 476 L88 1112 L82 1112 L82 1308 Q82 1318 72 1318 L30 1318 Q20 1318 20 1308 Z"/>
  <line class="fold" x1="20" y1="1112" x2="88" y2="1112"/>
  <line class="fold" x1="20" y1="1138" x2="82" y2="1138"/>
  <g class="glue-marks">
    <line x1="42" y1="515" x2="64" y2="510"/><line x1="42" y1="547" x2="64" y2="542"/>
    <line x1="42" y1="580" x2="64" y2="575"/><line x1="42" y1="612" x2="64" y2="607"/>
    <line x1="42" y1="645" x2="64" y2="640"/><line x1="42" y1="677" x2="64" y2="672"/>
    <line x1="42" y1="710" x2="64" y2="705"/><line x1="42" y1="742" x2="64" y2="737"/>
    <line x1="42" y1="775" x2="64" y2="770"/><line x1="42" y1="807" x2="64" y2="802"/>
    <line x1="42" y1="840" x2="64" y2="835"/><line x1="42" y1="872" x2="64" y2="867"/>
    <line x1="42" y1="905" x2="64" y2="900"/><line x1="42" y1="937" x2="64" y2="932"/>
    <line x1="42" y1="970" x2="64" y2="965"/><line x1="42" y1="1002" x2="64" y2="997"/>
    <line x1="42" y1="1035" x2="64" y2="1030"/><line x1="42" y1="1062" x2="64" y2="1057"/>
    <line x1="42" y1="1092" x2="64" y2="1087"/>
    <line x1="42" y1="1165" x2="64" y2="1160"/><line x1="42" y1="1197" x2="64" y2="1192"/>
    <line x1="42" y1="1230" x2="64" y2="1225"/><line x1="42" y1="1262" x2="64" y2="1257"/>
    <line x1="42" y1="1290" x2="64" y2="1285"/>
  </g>

  <!-- side panel left -->
  <path class="panel" d="M92 340 Q92 320 112 320 L145 320 Q152 320 155 330 A48 48 0 0 0 245 330 Q248 320 255 320 L288 320 Q308 320 308 340 L308 465 L92 465 Z"/>
  <rect class="panel" x="90" y="465" width="227" height="663"/>
  <path class="panel" d="M92 1128 L308 1128 L308 1288 Q308 1318 278 1318 L122 1318 Q92 1318 92 1288 Z"/>

  <!-- back panel -->
  <path class="panel" d="M325 268 Q325 243 350 243 L750 243 Q775 243 775 268 L775 465 L325 465 Z"/>
  <rect class="handle" x="452" y="318" width="196" height="66" rx="33"/>
  <line class="fold" x1="485" y1="384" x2="615" y2="384"/>
  <rect class="panel" x="317" y="465" width="466" height="663"/>
  <path class="panel" d="M325 1128 L775 1128 L775 1325 Q775 1350 750 1350 L350 1350 Q325 1350 325 1325 Z"/>

  <!-- side panel right -->
  <path class="panel" d="M793 340 Q793 320 813 320 L846 320 Q853 320 856 330 A48 48 0 0 0 946 330 Q949 320 956 320 L985 320 Q1005 320 1005 340 L1005 465 L793 465 Z"/>
  <rect class="panel" x="783" y="465" width="234" height="663"/>
  <path class="panel" d="M793 1128 L1005 1128 L1005 1288 Q1005 1318 975 1318 L823 1318 Q793 1318 793 1288 Z"/>

  <!-- front panel -->
  <path class="panel" d="M1025 268 Q1025 243 1050 243 L1450 243 Q1475 243 1475 268 L1475 465 L1025 465 Z"/>
  <rect class="handle" x="1142" y="310" width="216" height="75" rx="28"/>
  <line class="fold" x1="1170" y1="310" x2="1330" y2="310"/>
  <rect class="panel" x="1017" y="465" width="461" height="663"/>
  <path class="panel" d="M1025 1128 L1475 1128 L1475 1325 Q1475 1350 1450 1350 L1050 1350 Q1025 1350 1025 1325 Z"/>

  <!-- glue marks on flaps -->
  <g class="glue-marks">
    <line x1="110" y1="340" x2="125" y2="355"/><line x1="110" y1="370" x2="125" y2="385"/><line x1="110" y1="400" x2="125" y2="415"/><line x1="110" y1="425" x2="125" y2="440"/>
    <line x1="275" y1="340" x2="290" y2="355"/><line x1="275" y1="370" x2="290" y2="385"/><line x1="275" y1="400" x2="290" y2="415"/><line x1="275" y1="425" x2="290" y2="440"/>
    <line x1="810" y1="340" x2="825" y2="355"/><line x1="810" y1="370" x2="825" y2="385"/><line x1="810" y1="400" x2="825" y2="415"/><line x1="810" y1="425" x2="825" y2="440"/>
    <line x1="975" y1="340" x2="990" y2="355"/><line x1="975" y1="370" x2="990" y2="385"/><line x1="975" y1="400" x2="990" y2="415"/><line x1="975" y1="425" x2="990" y2="440"/>
    <line x1="125" y1="1155" x2="110" y2="1170"/><line x1="125" y1="1190" x2="110" y2="1205"/><line x1="125" y1="1225" x2="110" y2="1240"/><line x1="125" y1="1260" x2="110" y2="1275"/><line x1="125" y1="1285" x2="110" y2="1300"/>
    <line x1="292" y1="1155" x2="277" y2="1170"/><line x1="292" y1="1190" x2="277" y2="1205"/><line x1="292" y1="1225" x2="277" y2="1240"/><line x1="292" y1="1260" x2="277" y2="1275"/><line x1="292" y1="1285" x2="277" y2="1300"/>
    <line x1="825" y1="1155" x2="810" y2="1170"/><line x1="825" y1="1190" x2="810" y2="1205"/><line x1="825" y1="1225" x2="810" y2="1240"/><line x1="825" y1="1260" x2="810" y2="1275"/><line x1="825" y1="1285" x2="810" y2="1300"/>
    <line x1="992" y1="1155" x2="977" y2="1170"/><line x1="992" y1="1190" x2="977" y2="1205"/><line x1="992" y1="1225" x2="977" y2="1240"/><line x1="992" y1="1260" x2="977" y2="1275"/><line x1="992" y1="1285" x2="977" y2="1300"/>
    <line x1="1140" y1="265" x2="1155" y2="280"/><line x1="1170" y1="265" x2="1185" y2="280"/><line x1="1200" y1="275" x2="1215" y2="290"/>
    <line x1="1285" y1="265" x2="1300" y2="280"/><line x1="1315" y1="265" x2="1330" y2="280"/><line x1="1345" y1="270" x2="1360" y2="285"/>
    <line x1="1145" y1="415" x2="1160" y2="430"/><line x1="1170" y1="415" x2="1185" y2="430"/><line x1="1200" y1="425" x2="1215" y2="440"/>
    <line x1="1285" y1="415" x2="1300" y2="430"/><line x1="1315" y1="425" x2="1330" y2="440"/>
    <line x1="1110" y1="1155" x2="1095" y2="1178"/><line x1="1145" y1="1155" x2="1130" y2="1178"/><line x1="1180" y1="1155" x2="1165" y2="1178"/><line x1="1215" y1="1155" x2="1200" y2="1178"/>
    <line x1="1300" y1="1155" x2="1285" y2="1178"/><line x1="1335" y1="1155" x2="1320" y2="1178"/><line x1="1370" y1="1155" x2="1355" y2="1178"/><line x1="1405" y1="1155" x2="1390" y2="1178"/>
    <line x1="1110" y1="1305" x2="1095" y2="1328"/><line x1="1145" y1="1305" x2="1130" y2="1328"/><line x1="1180" y1="1305" x2="1165" y2="1328"/><line x1="1215" y1="1305" x2="1200" y2="1328"/>
    <line x1="1300" y1="1305" x2="1285" y2="1328"/><line x1="1335" y1="1305" x2="1320" y2="1328"/><line x1="1370" y1="1305" x2="1355" y2="1328"/><line x1="1405" y1="1305" x2="1390" y2="1328"/>
  </g>

  <!-- back and left side: photograph placeholder -->
  <g role="img" aria-label="Photograph of a pale lime margarita in a cocktail glass with a green leaf garnish, spanning the side and back panels">
    <rect x="196" y="392" width="112" height="73" fill="url(#photo-soft)"/>
    <rect x="196" y="465" width="522" height="663" fill="url(#photo-soft)"/>
  </g>

  <!-- front panel: photograph placeholder -->
  <rect x="1118" y="648" width="342" height="480" fill="url(#photo-soft)" role="img" aria-label="Photograph of a lime margarita in a cocktail glass with a leaf garnish"/>

  <!-- fold lines -->
  <g class="fold">
    <line x1="90" y1="465" x2="1478" y2="465"/>
    <line x1="90" y1="1128" x2="1478" y2="1128"/>
    <line x1="317" y1="465" x2="317" y2="1128"/>
    <line x1="783" y1="465" x2="783" y2="1128"/>
    <line x1="1017" y1="465" x2="1017" y2="1128"/>
  </g>

  <!-- right side panel: information -->
  <text class="script" x="900" y="528" font-size="40" text-anchor="middle">Stay Fresh!</text>
  <g class="body-copy" font-size="10.5" text-anchor="middle">
    <text x="902" y="563">Lorem ipsum dolor sit amet, consectetuer</text>
    <text x="902" y="577">adipiscing elit, sed diam nonummy nibh</text>
    <text x="902" y="591">euismod tincidunt ut laoreet dolore magna</text>
    <text x="902" y="604">aliquam erat volutpat.</text>
    <text x="902" y="630">Ut wisi enim ad minim veniam, quis nostrud</text>
    <text x="902" y="643">exerci tation ullamcorper suscipit lobortis</text>
    <text x="902" y="657">nisl ut aliquip ex ea commodo consequat.</text>
    <text x="902" y="670">Duis autem vel eum iriure dolor in hendrerit</text>
    <text x="902" y="684">in vulputate velit esse molestie consequat.</text>
  </g>

  <!-- flavour band across side and front -->
  <rect x="785" y="710" width="426" height="76" fill="url(#band)"/>
  <line x1="785" y1="715" x2="1211" y2="715" stroke="#1d4a0c" stroke-width="3"/>
  <line x1="785" y1="781" x2="1211" y2="781" stroke="#1d4a0c" stroke-width="3"/>
  <line class="fold" x1="1017" y1="710" x2="1017" y2="786"/>
  <text class="flavour" x="900" y="758" font-size="30" text-anchor="middle" style="letter-spacing:5px">MARGARITA</text>
  <text class="flavour" x="1112" y="758" font-size="30" text-anchor="middle" style="letter-spacing:5px">MARGARITA</text>

  <text class="small-caps" x="904" y="807" font-size="11" text-anchor="middle">Taste Well With</text>
  <rect x="785" y="818" width="230" height="47" fill="var(--cream)"/>
  <g fill="#9a8a3a">
    <ellipse cx="830" cy="837" rx="13" ry="8"/>
    <ellipse cx="902" cy="837" rx="11" ry="9"/>
    <path d="M956 832 L982 832 L975 845 L963 845 Z"/>
  </g>
  <g class="tiny" font-size="7" fill="#9a8a3a" text-anchor="middle">
    <text x="832" y="859">Veggies</text><text x="902" y="859">Chicken</text><text x="970" y="859">Guacamole</text>
  </g>

  <!-- open here tear panel -->
  <path d="M836 882 L836 985 L860 1000 L860 1050 Q860 1072 880 1072 L918 1072 Q940 1072 940 1050 L940 1000 L964 985 L964 882" fill="none" stroke="var(--cut)" stroke-width="1.6" stroke-dasharray="4 3"/>
  <path d="M860 1000 Q900 975 940 1000" fill="none" stroke="var(--cut)" stroke-width="1.6" stroke-dasharray="4 3"/>
  <line class="fold" x1="836" y1="881" x2="964" y2="881"/>
  <text class="tiny" x="950" y="900" font-size="11">B</text>
  <text class="tiny" x="920" y="1015" font-size="11">A</text>
  <text class="small-caps" x="902" y="1041" font-size="7" text-anchor="middle">OPEN HERE</text>
  <text class="tiny" x="902" y="1051" font-size="5" text-anchor="middle">10% alc./vol</text>
  <rect x="846" y="913" width="108" height="55" fill="#9ed36a"/>
  <rect x="850" y="918" width="22" height="30" fill="#ffffff"/>
  <text class="tiny" x="881" y="945" font-size="12">=</text>
  <text class="tiny" x="897" y="946" font-size="16">4 x</text>
  <rect x="930" y="925" width="8" height="27" rx="2" fill="#111"/>
  <rect x="932" y="916" width="4" height="10" fill="#111"/>
  <text class="tiny" x="852" y="964" font-size="6">1 cask</text>
  <text class="tiny" x="880" y="964" font-size="6">=</text>
  <text class="tiny" x="892" y="964" font-size="6">Four 750ml Bottles</text>

  <text class="volume-num" x="814" y="1066" font-size="36" text-anchor="middle">3</text>
  <text class="volume-unit" x="826" y="1088" font-size="15" text-anchor="middle">LITERS</text>
  <text class="tiny" x="826" y="1096" font-size="5" text-anchor="middle">SERVED CHILLED</text>

  <text class="brand-hero" font-size="28" transform="translate(996 1098) rotate(-90)">Velora</text>

  <!-- front top flap -->
  <text class="brand-hero" x="1043" y="292" font-size="30">Velora</text>
  <text class="tiny" x="1045" y="300" font-size="4.5">love and elegance within yourself</text>
  <rect x="1048" y="325" width="38" height="22" fill="#2a2a2a" role="img" aria-label="Illustration of agave, lime and sombrero"/>
  <text class="contains-title" x="1048" y="360" font-size="11">Contains</text>
  <g class="contains-item" font-size="6.5">
    <text x="1052" y="368">• MEXICAN INSPIRATION</text>
    <text x="1052" y="375">• TEQUILA</text>
    <text x="1052" y="382">• LIME JUICE</text>
  </g>
  <rect x="1027" y="406" width="114" height="44" fill="url(#band)"/>
  <text class="flavour" x="1083" y="434" font-size="16" text-anchor="middle" style="letter-spacing:2px">MARGARITA</text>
  <circle cx="1416" cy="316" r="42" fill="none" stroke="var(--leaf)" stroke-width="3"/>
  <text class="tiny" x="1378" y="389" font-size="4.5">BEST BEFORE/PRODUCTION CODE</text>
  <rect x="1330" y="392" width="148" height="63" fill="var(--grey-box)"/>

  <!-- front panel -->
  <text class="brand-hero" x="1218" y="606" font-size="112" text-anchor="middle">Velora</text>
  <text class="tagline" x="1219" y="633" font-size="12" text-anchor="middle">LOVE AND ELEGANCE WITHIN YOURSELF</text>

  <circle cx="1371" cy="962" r="43" fill="none" stroke="var(--leaf-light)" stroke-width="3"/>

  <rect x="1047" y="850" width="70" height="38" fill="#2a2a2a" role="img" aria-label="Illustration of agave, lime and sombrero"/>
  <text class="contains-title" x="1050" y="916" font-size="22">Contains</text>
  <g class="contains-item" font-size="12">
    <text x="1055" y="929">• MEXICAN INSPIRATION</text>
    <text x="1055" y="943">• TEQUILA</text>
    <text x="1055" y="957">• LIME JUICE</text>
  </g>
  <text class="volume-num" x="1062" y="1055" font-size="58" text-anchor="middle">3</text>
  <text class="volume-unit" x="1080" y="1088" font-size="24" text-anchor="middle">LITERS</text>
  <text class="tiny" x="1080" y="1099" font-size="6.5" letter-spacing="1" text-anchor="middle">SERVED CHILLED</text>
  <text class="abv" x="1422" y="1086" font-size="12" text-anchor="middle">10% alc./vol</text>
</svg>
</body>
</html>
```